Custom Manufacturing Company square space website design

I own a custom manufacturing company that uses precision cutting technology to manufacture project components over a couple industries. We have an industrial CNC router and state of the art edge bander and cut a lot of cabinetry components for cabinet shops, builders, closet companies, ect. We offer design and assembly for any cabinetry or can build cabinets to spec. We also cut components for other industries out of wood, plastics, acryclics, ect. We offer design engineering services, product development protype services. we have a 3D printer farm. We want our communicate trust, dependability, and the value we place on client relationships.

We essentially want a credibility website. Landing page and drops downs for services we offer, capabilites, about us, contact

```html
<!DOCTYPE html>
<html lang="en">
<head>
<meta charset="utf-8">
<title>Northline CNC</title>
<link href="https://fonts.googleapis.com/css2?family=Montserrat:wght@400;500;600;700;800&display=swap" rel="stylesheet">
<style>
:root{
  --ink:#0d0d0d;
  --white:#ffffff;
  --text:#2a2a2a;
  --muted:#555555;
  --footer:#1a1a1a;
}
*{box-sizing:border-box;margin:0;padding:0}
html,body{width:1200px;height:3684px;overflow:hidden}
body{position:relative;font-family:'Montserrat',sans-serif;color:var(--text);background:var(--white)}
.abs{position:absolute}
svg{display:block;flex-shrink:0}

/* header */
.brand{display:flex;align-items:center;gap:12px;font-weight:700;letter-spacing:3px;color:var(--ink);white-space:nowrap}
.brand-mark{width:34px;height:34px;border:3px solid currentColor}
.header-brand{left:112px;top:48px;font-size:26px}
.topbar{left:420px;top:0;width:780px;height:57px;background:var(--ink);clip-path:polygon(0 0,100% 0,100% 100%,36px 100%)}
.topbar-item{display:flex;align-items:center;gap:12px;color:var(--white);font-size:14px;font-weight:600;top:0;height:57px;white-space:nowrap}
.nav{top:84px;left:433px;display:flex;gap:57px;font-size:16px;font-weight:600;color:var(--ink);align-items:center}
.nav .active{text-decoration:underline;text-underline-offset:4px}
.nav-cta{left:1012px;top:76px;width:112px;height:37px;background:var(--ink);color:var(--white);font-size:16px;font-weight:700;display:flex;align-items:center;justify-content:center}

/* hero */
.hero{left:0;top:146px;width:1200px;height:549px;background:linear-gradient(90deg,#c9cccd 0%,#6b6c6e 30%,#4a4b4d 60%,#7c7d7f 100%)}
.hero-title{left:110px;top:330px;color:var(--white)}
.hero-title .small{font-size:30px;font-weight:600}
.hero-title .big{font-size:46px;font-weight:700;margin-top:6px}
.btn-light{background:var(--white);color:var(--ink);font-weight:700;display:flex;align-items:center;justify-content:center}
.hero-btn{left:111px;top:444px;width:138px;height:37px;font-size:15px}
.hero-dots{left:1141px;top:325px;display:flex;flex-direction:column;gap:14px}
.hero-dots span{width:4px;height:26px;background:var(--white)}

/* about */
.h2{font-size:32px;font-weight:700;color:var(--ink);letter-spacing:.5px}
.h2-rule{height:4px;width:106px;background:var(--ink);margin-top:4px}
.about-title{left:109px;top:776px}
.about-text{left:110px;top:834px;width:447px;font-size:14.5px;line-height:31px;text-align:justify}
.btn-dark{background:var(--ink);color:var(--white);font-weight:700;display:flex;align-items:center;justify-content:center}
.about-btn{left:109px;top:1090px;width:132px;height:37px;font-size:15px}
.about-frame{left:658px;top:818px;width:420px;height:317px;border-right:6px solid var(--ink);border-bottom:6px solid var(--ink)}
.about-photo{left:645px;top:805px;width:421px;height:316px;background:linear-gradient(135deg,#3d4a44,#2c3a4a 50%,#b9c0c5);border:3px solid var(--white)}

/* capabilities */
.cap-photo{left:0;top:1216px;width:563px;height:482px;background:linear-gradient(135deg,#f1f1f1,#d9d9db 50%,#4a4a4a 80%,#8a8a8a)}
.cap-panel{left:568px;top:1216px;width:632px;height:482px;background:linear-gradient(135deg,#3a3a3a,#2a2a2a 60%,#4b4b4b)}
.cap-title{left:600px;top:1260px;color:var(--white)}
.cap-title .h2{color:var(--white)}
.cap-title .h2-rule{background:var(--white);width:108px}
.cap-text{left:601px;top:1323px;width:455px;color:var(--white);font-size:14px;line-height:31px}
.cap-list{left:601px;top:1460px;list-style:none;color:var(--white);font-size:14px}
.cap-list li{display:flex;align-items:center;gap:14px;height:34px}
.cap-btn{left:600px;top:1619px;width:132px;height:36px;font-size:15px}

/* services */
.services-title{left:0;top:1788px;width:1200px;text-align:center}
.services-title .h2-rule{margin:6px auto 0;width:106px}
.card{top:1877px;width:308px;height:349px;background:var(--white);box-shadow:0 2px 8px rgba(0,0,0,.18)}
.card-img{position:absolute;left:10px;top:14px;width:287px;height:284px}
.card-label{position:absolute;left:0;bottom:16px;width:100%;text-align:center;font-weight:600;font-size:17px;color:var(--ink)}
.arrow{top:2048px}

/* contact */
.contact{left:0;top:2330px;width:1200px;height:614px;background:linear-gradient(135deg,#5a5a5a,#3a3a3a 50%,#4d4d4d)}
.contact-arc{left:93px;top:2403px;width:336px;height:468px;border-top:6px solid var(--white);border-right:6px solid var(--white);border-top-right-radius:80px}
.contact-photo{left:93px;top:2412px;width:326px;height:459px;border-top-right-radius:74px;background:linear-gradient(160deg,#9b8a74,#5b6a78 50%,#2b3340)}
.contact-title{left:479px;top:2430px;color:var(--white);font-size:32px;font-weight:700}
.field{left:482px;width:315px;color:var(--white);font-size:16px;font-weight:700;border-bottom:2px solid var(--white);padding-bottom:8px}
.submit{left:484px;top:2773px;width:108px;height:31px;font-size:14px}
.info-box{left:826px;top:2412px;width:261px;height:452px;border:3px solid var(--white)}
.info-row{position:absolute;left:0;width:100%;border-bottom:3px solid var(--white);color:var(--white)}
.info-row:last-child{border-bottom:none}
.info-label{font-size:14px;font-weight:700;margin:0 0 14px 20px}
.info-value{display:flex;gap:8px;align-items:flex-start;font-size:15px;font-weight:700;margin-left:20px;line-height:24px;white-space:nowrap}
.info-value.email{font-size:12.5px}

/* newsletter & footer */
.footer{left:0;top:3200px;width:1200px;height:484px;background:var(--footer)}
.news{left:110px;top:3045px;width:977px;height:252px;background:var(--white)}
.news-title{left:0;top:3100px;width:1200px;text-align:center}
.news-title .h2{font-size:29px}
.news-title .h2-rule{margin:4px auto 0;width:106px}
.news-form{left:163px;top:3156px;width:870px;height:77px;border:1px solid #888;display:flex}
.news-input{flex:1;display:flex;align-items:center;padding-left:38px;font-size:15px;color:var(--text)}
.news-btn{width:139px;font-size:15px}
.footer-brand{left:112px;top:3388px;width:260px;flex-direction:column;gap:22px;font-size:24px;color:var(--white)}
.footer-brand .brand-mark{width:90px;height:62px}
.socials{left:186px;top:3546px;display:flex;gap:8px}
.socials span{width:22px;height:22px;background:var(--white)}
.fcol{top:3384px;color:var(--white)}
.fcol h4{font-size:17px;font-weight:700;margin-bottom:16px}
.fcol a{display:block;font-size:16px;color:var(--white);text-decoration:none;margin-bottom:17px}
.fcontact{display:flex;gap:18px;font-size:15px;line-height:24px;margin-bottom:24px;align-items:flex-start;white-space:nowrap}
.footer-rule{left:112px;top:3618px;width:977px;height:1px;background:#888}
.copy{left:0;top:3643px;width:1200px;text-align:center;color:var(--white);font-size:15px}
</style>
</head>
<body>

<!-- Header -->
<div class="abs brand header-brand"><span class="brand-mark"></span>NORTHLINE CNC</div>
<div class="abs topbar"></div>
<div class="abs topbar-item" style="left:503px">
  <svg width="24" height="24" viewBox="0 0 24 24"><rect width="24" height="24" rx="3" fill="#fff"/><path d="M12 4a5 5 0 0 0-5 5c0 4 5 10 5 10s5-6 5-10a5 5 0 0 0-5-5zm0 7a2 2 0 1 1 0-4 2 2 0 0 1 0 4z" fill="#000"/></svg>
  <span style="line-height:21px">Lorem Ipum<br>USA - 473916</span>
</div>
<div class="abs topbar-item" style="left:709px">
  <svg width="22" height="22" viewBox="0 0 24 24"><rect width="24" height="24" rx="3" fill="#fff"/><path d="M7 5l3 0 1 4-2 1c1 2 3 4 5 5l1-2 4 1v3c0 1-1 2-2 2C10 19 5 14 5 7c0-1 1-2 2-2z" fill="#000"/></svg>
  <span>+1 888 888 8888</span>
</div>
<div class="abs topbar-item" style="left:931px">
  <svg width="22" height="22" viewBox="0 0 24 24"><rect width="24" height="24" rx="3" fill="#fff"/><path d="M5 7h14v10H5z M5 7l7 6 7-6" fill="none" stroke="#000" stroke-width="1.8"/></svg>
  <span>info@northlinecnc.example</span>
</div>
<nav class="abs nav">
  <span class="active">Home</span><span>Services &nbsp;We Offer</span><span>Capabilities</span><span>About Us</span>
</nav>
<div class="abs nav-cta">CONTACT</div>

<!-- Hero -->
<div class="abs hero" role="img" aria-label="Modern dark grey kitchen with wall cabinets, countertop and bar stools"></div>
<div class="abs hero-title"><div class="small">WELCOME TO</div><div class="big">NORTHLINE CNC</div></div>
<div class="abs btn-light hero-btn">GET STARTED</div>
<div class="abs hero-dots"><span></span><span></span><span></span></div>

<!-- About -->
<div class="abs about-title"><div class="h2">ABOUT US</div><div class="h2-rule"></div></div>
<p class="abs about-text">Lorem ipsum dolor sit amet, consectetur adipiscing elit, sed do eiusmod tempor incididunt ut labore et dolore magna aliqua. Ut enim ad minim veniam, quis nostrud exercitation ullamco laboris nisi ut aliquip ex ea commodo consequat. Duis aute irure dolor in reprehenderit in voluptate velit esse cillum dolore eu fugiat nulla pariatur. Excepteur sint occaecat cupidatat non proident, sunt in culpa qui officia deserunt mollit anim id est laborum</p>
<div class="abs btn-dark about-btn">READ MORE</div>
<div class="abs about-frame"></div>
<div class="abs about-photo" role="img" aria-label="Business owner in a suit working at a laptop in an office"></div>

<!-- Capabilities -->
<div class="abs cap-photo" role="img" aria-label="White kitchen cabinets with open drawers and dark countertop"></div>
<div class="abs cap-panel" role="img" aria-label="Dimmed kitchen interior background"></div>
<div class="abs cap-title"><div class="h2">CAPABILITIES</div><div class="h2-rule"></div></div>
<p class="abs cap-text">Lorem ipsum dolor sit amet, consectetur adipiscing elit, sed do eiusmod tempor incididunt ut labore et dolore magna aliqua. Ut enim ad minim veniam, quis nostrud exercitation ullamco laboris nisi ut aliquip ex ea commodo consequat.</p>
<ul class="abs cap-list">
  <li><svg width="14" height="14" viewBox="0 0 14 14"><circle cx="7" cy="7" r="7" fill="#fff"/><path d="M4 7h6M7 4l3 3-3 3" stroke="#222" stroke-width="1.6" fill="none"/></svg>Lorem ipsum dolor sit amet, consectetur adipiscing elit</li>
  <li><svg width="14" height="14" viewBox="0 0 14 14"><circle cx="7" cy="7" r="7" fill="#fff"/><path d="M4 7h6M7 4l3 3-3 3" stroke="#222" stroke-width="1.6" fill="none"/></svg>Lorem ipsum dolor sit amet, consectetur adipiscing elit</li>
  <li><svg width="14" height="14" viewBox="0 0 14 14"><circle cx="7" cy="7" r="7" fill="#fff"/><path d="M4 7h6M7 4l3 3-3 3" stroke="#222" stroke-width="1.6" fill="none"/></svg>Lorem ipsum dolor sit amet, consectetur adipiscing elit</li>
  <li style="margin-top:8px"><svg width="14" height="14" viewBox="0 0 14 14"><circle cx="7" cy="7" r="7" fill="#fff"/><path d="M4 7h6M7 4l3 3-3 3" stroke="#222" stroke-width="1.6" fill="none"/></svg>Lorem ipsum dolor sit amet, consectetur adipiscing elit</li>
</ul>
<div class="abs btn-light cap-btn">READ MORE</div>

<!-- Services -->
<div class="abs services-title"><div class="h2">SERVICES WE OFFER</div><div class="h2-rule"></div></div>
<svg class="abs arrow" style="left:46px" width="20" height="24" viewBox="0 0 20 24"><path d="M14 3L5 12l9 9" stroke="#111" stroke-width="4" fill="none"/></svg>
<svg class="abs arrow" style="left:1125px" width="20" height="24" viewBox="0 0 20 24"><path d="M6 3l9 9-9 9" stroke="#111" stroke-width="4" fill="none"/></svg>
<div class="abs card" style="left:113px"><div class="card-img" role="img" aria-label="Kitchen with dark wood cabinets and island" style="background:linear-gradient(160deg,#6e3a2a,#4a2418 55%,#a1561f)"></div><div class="card-label">WOOD CABINETS</div></div>
<div class="abs card" style="left:445px"><div class="card-img" role="img" aria-label="Blue and white plastic drawer cabinets" style="background:linear-gradient(160deg,#f4f4f4,#d8e2e8 55%,#2f7a98)"></div><div class="card-label">PLASTIC CABINETS</div></div>
<div class="abs card" style="left:776px"><div class="card-img" role="img" aria-label="Bright kitchen with white acrylic cabinets" style="background:linear-gradient(160deg,#eef0ee,#cfd4d0 55%,#7a4a30)"></div><div class="card-label">ACRYLICS &nbsp;CABINETS</div></div>

<!-- Contact -->
<div class="abs contact" role="img" aria-label="Dimmed kitchen interior background"></div>
<div class="abs contact-arc"></div>
<div class="abs contact-photo" role="img" aria-label="Technician fitting a cabinet door with a screwdriver"></div>
<div class="abs contact-title">CONTACT US</div>
<div class="abs field" style="top:2508px">Full Name</div>
<div class="abs field" style="top:2591px">Email</div>
<div class="abs field" style="top:2689px">Message</div>
<div class="abs btn-light submit">SUBMIT</div>
<div class="abs info-box">
  <div class="info-row" style="top:0;height:129px;padding-top:34px">
    <div class="info-label">EMAIL US</div>
    <div class="info-value email"><svg width="20" height="20" viewBox="0 0 24 24" style="margin-top:2px"><rect width="24" height="24" rx="3" fill="#fff"/><path d="M5 7h14v10H5z M5 7l7 6 7-6" fill="none" stroke="#333" stroke-width="1.8"/></svg>info@northlinecnc.example</div>
  </div>
  <div class="info-row" style="top:129px;height:158px;padding-top:42px">
    <div class="info-label">LOCATED IN</div>
    <div class="info-value"><svg width="20" height="20" viewBox="0 0 24 24" style="margin-top:3px"><rect width="24" height="24" rx="3" fill="#fff"/><path d="M12 4a5 5 0 0 0-5 5c0 4 5 10 5 10s5-6 5-10a5 5 0 0 0-5-5zm0 7a2 2 0 1 1 0-4 2 2 0 0 1 0 4z" fill="#333"/></svg><span>Lorem Ipum<br>USA - 473916</span></div>
  </div>
  <div class="info-row" style="top:287px;height:160px;padding-top:40px">
    <div class="info-label" style="margin-bottom:24px">CALL US</div>
    <div class="info-value"><svg width="20" height="20" viewBox="0 0 24 24" style="margin-top:2px"><rect width="24" height="24" rx="3" fill="#fff"/><path d="M7 5l3 0 1 4-2 1c1 2 3 4 5 5l1-2 4 1v3c0 1-1 2-2 2C10 19 5 14 5 7c0-1 1-2 2-2z" fill="#333"/></svg>+1 888 888 8888</div>
  </div>
</div>

<!-- Newsletter & footer -->
<div class="abs footer"></div>
<div class="abs news"></div>
<div class="abs news-title"><div class="h2">NEWSLETTER SIGNUP</div><div class="h2-rule"></div></div>
<div class="abs news-form"><div class="news-input">Enter Your Email Address</div><div class="btn-dark news-btn">SUBSCRIBE</div></div>

<div class="abs brand footer-brand"><span class="brand-mark"></span>NORTHLINE CNC</div>
<div class="abs socials"><span></span><span></span><span></span><span></span></div>

<div class="abs fcol" style="left:459px"><h4>QUICK LINKS</h4><a>Home</a><a>Service We &nbsp;Offer</a><a>Capabilities</a><a>About Us</a><a>Contact</a></div>
<div class="abs fcol" style="left:662px"><h4>HELP LINKS</h4><a>Privacy Policy</a><a>Terms &amp; Conditions</a></div>
<div class="abs fcol" style="left:884px"><h4>CONTACT US</h4>
  <div class="fcontact"><svg width="24" height="24" viewBox="0 0 24 24"><rect width="24" height="24" rx="3" fill="#fff"/><path d="M12 4a5 5 0 0 0-5 5c0 4 5 10 5 10s5-6 5-10a5 5 0 0 0-5-5zm0 7a2 2 0 1 1 0-4 2 2 0 0 1 0 4z" fill="#1a1a1a"/></svg><span>Lorem Ipum<br>USA - 473916</span></div>
  <div class="fcontact"><svg width="22" height="22" viewBox="0 0 24 24"><rect width="24" height="24" rx="3" fill="#fff"/><path d="M7 5l3 0 1 4-2 1c1 2 3 4 5 5l1-2 4 1v3c0 1-1 2-2 2C10 19 5 14 5 7c0-1 1-2 2-2z" fill="#1a1a1a"/></svg><span>+1 888 888 8888</span></div>
  <div class="fcontact"><svg width="22" height="22" viewBox="0 0 24 24"><rect width="24" height="24" rx="3" fill="#fff"/><path d="M5 7h14v10H5z M5 7l7 6 7-6" fill="none" stroke="#1a1a1a" stroke-width="1.8"/></svg><span>info@northlinecnc.example</span></div>
</div>
<div class="abs footer-rule"></div>
<div class="abs copy">© 2023 &nbsp;Northline CNC. All rights reserved.</div>

</body>
</html>
```